Executive Business Card for Healthcare Company [Need Today]

I need a business card design for a healthcare company. The only branding the company has thus far is a logo. The cards will be utilized by company executives. The design I envision will be vibrant and appealing but with a corporate feel. They shouldn't be too casual or playful. I would like to complete this project TODAY if possible.

Target Market(s)

Healthcare vendors, other executives in healthcare and pharmaceuticals

Industry/Entity Type

Pharmaceutical

Contact Information for Business Card

See attachment

Font styles to use
Serif
Sans Serif

Colors

Designer to choose colors to be used in the design.

```html
<!DOCTYPE html>
<html lang="en">
<head>
<meta charset="utf-8">
<title>Corvane Therapeutics – Executive Business Card</title>
<link rel="stylesheet" href="https://fonts.googleapis.com/css2?family=Mulish:wght@400;700;800&display=swap">
<style>
  :root {
    --backdrop: #e9e6e1;
    --card-black: #0c0c0c;
    --card-white: #f4f5f6;
    --brand-teal: #1ab3b6;
    --brand-green: #5cc79a;
    --ink: #141414;
    --ink-soft: #3a3a3a;
    --on-dark: #f2f2f2;
  }
  * { box-sizing: border-box; margin: 0; padding: 0; }
  html, body {
    width: 1200px; height: 800px; overflow: hidden;
    background: var(--backdrop);
    font-family: "Mulish", sans-serif;
  }
  .canvas {
    width: 1200px; height: 800px;
    display: flex; align-items: center; justify-content: center; gap: 50px;
  }
  .card {
    width: 525px; height: 300px; position: relative; overflow: hidden;
    border-radius: 4px;
    box-shadow: 0 10px 28px rgba(0,0,0,.18);
  }

  /* Front */
  .card--front {
    background: var(--card-black);
    display: flex; align-items: center; justify-content: center; gap: 22px;
  }
  .brand-ring {
    width: 104px; height: 104px; border-radius: 50%;
    border: 9px solid var(--brand-green);
  }
  .brand-name {
    color: var(--brand-teal); font-weight: 400;
    font-size: 34px; line-height: 1.1; letter-spacing: .5px;
  }

  /* Back */
  .card--back { background: var(--card-white); }
  .accent-band {
    position: absolute; top: 0; left: 0; width: 340px; height: 12px;
    background: var(--brand-green);
    clip-path: polygon(0 0, 100% 0, calc(100% - 12px) 100%, 0 100%);
  }
  .identity { position: absolute; left: 32px; top: 34px; color: var(--ink); }
  .identity__name { font-size: 27px; font-weight: 800; letter-spacing: .2px; }
  .identity__title { font-size: 15px; color: var(--ink-soft); margin-top: 2px; }
  .company { position: absolute; left: 32px; top: 122px; color: var(--ink); }
  .company__name { font-size: 15px; font-weight: 700; }
  .company__address { font-size: 14px; color: var(--ink-soft); margin-top: 2px; }

  .back-mark {
    position: absolute; right: 42px; top: 70px;
    width: 122px; height: 122px; border-radius: 50%;
    border: 8px solid var(--brand-green);
    display: flex; align-items: center; justify-content: center;
  }
  .back-mark__name { color: var(--brand-teal); font-size: 18px; font-weight: 400; }

  .contact-bar {
    position: absolute; left: 0; right: 0; bottom: 0; height: 88px;
    background: var(--card-black);
    display: flex; justify-content: space-between; align-items: center;
    padding: 0 30px;
  }
  .contact {
    display: flex; flex-direction: column; align-items: center; gap: 8px;
    color: var(--on-dark); font-size: 15px; letter-spacing: .3px;
  }
  .contact__icon {
    width: 22px; height: 22px; border-radius: 50%;
    background: var(--brand-green);
    display: flex; align-items: center; justify-content: center;
  }
  .contact__icon svg { width: 13px; height: 13px; }
</style>
</head>
<body>
<main class="canvas">
  <section class="card card--front" aria-label="Card front">
    <div class="brand-ring"></div>
    <div class="brand-name">corvane therapeutics</div>
  </section>

  <section class="card card--back" aria-label="Card back">
    <div class="accent-band"></div>
    <div class="identity">
      <h1 class="identity__name">Daniel Marsh</h1>
      <p class="identity__title">Senior Director of Marketing</p>
    </div>
    <div class="company">
      <p class="company__name">Corvane Therapeutics, LLC</p>
      <p class="company__address">118 Linden Row, Milbrook, GA 30655</p>
    </div>
    <div class="back-mark"><span class="back-mark__name">corvane</span></div>

    <div class="contact-bar">
      <div class="contact">
        <span class="contact__icon">
          <svg viewBox="0 0 24 24"><path fill="#0c0c0c" d="M6.6 10.8a15.1 15.1 0 0 0 6.6 6.6l2.2-2.2a1 1 0 0 1 1-.25 11.4 11.4 0 0 0 3.6.57 1 1 0 0 1 1 1V20a1 1 0 0 1-1 1A17 17 0 0 1 3 4a1 1 0 0 1 1-1h3.5a1 1 0 0 1 1 1c0 1.25.2 2.45.57 3.57a1 1 0 0 1-.25 1z"/></svg>
        </span>
        <span class="contact__text">555-201-4470</span>
      </div>
      <div class="contact">
        <span class="contact__icon">
          <svg viewBox="0 0 24 24"><rect x="3" y="5" width="18" height="14" rx="2" fill="#0c0c0c"/><path d="M4 7l8 6 8-6" fill="none" stroke="#5cc79a" stroke-width="2"/></svg>
        </span>
        <span class="contact__text">dmarsh@corvanerx.com</span>
      </div>
      <div class="contact">
        <span class="contact__icon">
          <svg viewBox="0 0 24 24"><rect x="6" y="2" width="12" height="20" rx="2" fill="#0c0c0c"/><rect x="8" y="4.5" width="8" height="12.5" fill="#5cc79a"/></svg>
        </span>
        <span class="contact__text">555-201-8835</span>
      </div>
    </div>
  </section>
</main>
</body>
</html>
```